Design for three pages of a 12-page 4-color 8.5 x 11 magazine-type booklet

We will be taking the information from a webpage at brightmeadowcivic.org and putting it into a 12-page 4-color 8.5 x 11 magazine-type booklet that will look like an upscale company report. I need to have a design in Photoshop for the cover and two inside pages that I can use as the template for the pages. I likely will also need help putting it together once I start putting the contents into the pages. I may just decide on the content and have the designer create the booklet as an additional freelance contract. First, I need a design for (1) the front cover, (2) one information page taken from information on http://www.brightmeadowcivic.org/bmci-project-management-staff/, and (3) one of the pages that has a researcher from this page on it: http://www.brightmeadowcivic.org/teaching-people-how-to-have/. That's designs for three pages. The designs have to be very professional looking and businesslike. We will be using the booklet to pitch to foundations and philanthropists. The work on the publication itself would be additional freelance work on an hourly basis.

Font styles to use
Serif

Colors

Designer to choose colors to be used in the design.

Requirements
Must have
• Professional look

```html
<!DOCTYPE html>
<html lang="en">
<head>
<meta charset="utf-8">
<title>BMCI Booklet – Staff and Program Spread</title>
<link href="https://fonts.googleapis.com/css2?family=Montserrat:ital,wght@0,400;0,600;0,700;1,400;1,600;1,700&family=Raleway:ital,wght@0,300;0,400;1,300;1,400&display=swap" rel="stylesheet">
<style>
  :root{
    --backdrop:#3d4a50;
    --paper:#f7f7f8;
    --navy:#3b3a8f;
    --ink:#3c3c44;
    --muted:#7a7a84;
    --rule:#b9bad4;
    --white:#ffffff;
  }
  *{box-sizing:border-box;margin:0;padding:0}
  html,body{width:1200px;height:840px;overflow:hidden}
  body{background:var(--backdrop);font-family:"Raleway",sans-serif;color:var(--ink);position:relative}

  .spread{position:absolute;left:40px;top:58px;width:1120px;height:724px;display:flex;box-shadow:0 10px 30px rgba(0,0,0,.35)}
  .page{position:relative;width:560px;height:724px;background:var(--paper);overflow:hidden}
  .page--left{background:linear-gradient(to right,var(--paper) 88%,#e4e4e8 100%)}
  .page--right{background:linear-gradient(to left,var(--paper) 88%,#e6e6ea 100%)}

  .page-title{position:absolute;left:40px;top:40px;font-family:"Montserrat",sans-serif;font-style:italic;font-weight:700;font-size:24px;color:#1f1f2a;letter-spacing:-.2px}
  .title-rule{position:absolute;left:40px;top:80px;width:480px;height:4px;background:var(--navy)}
  .intro{position:absolute;left:40px;top:92px;width:470px;font-style:italic;font-weight:300;font-size:9.5px;line-height:1.4;color:var(--muted)}

  .staff-card{position:absolute;width:150px}
  .staff-photo{width:150px;height:96px;border-radius:1px}
  .staff-role{margin-top:8px;font-family:"Montserrat",sans-serif;font-weight:700;font-size:9px;letter-spacing:.3px;color:var(--navy);text-transform:uppercase}
  .staff-name{font-family:"Montserrat",sans-serif;font-style:italic;font-weight:600;font-size:7.5px;color:#2a2a33;padding-bottom:4px;border-bottom:1px solid var(--rule)}
  .staff-bio{margin-top:5px;font-weight:300;font-size:7.4px;line-height:1.45;color:var(--ink)}

  .photo-portrait-a{background:linear-gradient(135deg,#4a3426,#8a6a52 55%,#2e2119)}
  .photo-portrait-b{background:linear-gradient(135deg,#e8e6e0,#c9b48a 55%,#dcd8cf)}
  .photo-portrait-c{background:linear-gradient(135deg,#4e6a2e,#c98a5a 55%,#7a8a44)}
  .photo-portrait-d{background:linear-gradient(135deg,#1d5a86,#6a4030 55%,#2a6e9e)}
  .photo-portrait-e{background:linear-gradient(135deg,#2a2a28,#b8866a 55%,#3a3833)}
  .photo-books{background:linear-gradient(135deg,#2a3a6e,#c8722a 50%,#4a6ab0)}

  .url{position:absolute;font-family:"Montserrat",sans-serif;font-weight:600;font-size:7.5px;color:#2a2a33;letter-spacing:.2px}
  .page--left .url{left:40px;bottom:36px}
  .page--right .url{right:40px;bottom:36px}
  .wedge{position:absolute;bottom:24px}
  .page--left .wedge{right:0}
  .page--right .wedge{left:0}

  .hero-photo{position:absolute;left:0;top:0;width:560px;height:336px;background:linear-gradient(160deg,#b9c4cf 0%,#5d6b78 40%,#2f3944 75%,#4e5a66 100%)}
  .hero-banner{position:absolute;left:190px;top:262px;width:370px;height:118px;background:var(--navy);color:var(--white);padding:24px 28px;font-family:"Montserrat",sans-serif}
  .hero-banner span{display:block;font-size:23px;font-weight:400;line-height:1.2}
  .hero-banner strong{display:block;font-size:23px;font-weight:700;letter-spacing:.5px;line-height:1.2}

  .program-text{position:absolute;left:40px;top:404px;width:480px;font-weight:300;font-size:8.6px;line-height:1.5}
  .program-link{position:absolute;left:40px;top:478px;font-family:"Montserrat",sans-serif;font-weight:700;font-size:12px;color:var(--navy)}
  .program-sub{position:absolute;left:40px;top:496px;font-size:10px;color:var(--ink)}

  .topic-list{position:absolute;list-style:none}
  .topic-list--a{left:40px;top:524px;width:240px}
  .topic-list--b{left:300px;top:560px;width:220px}
  .topic-list li{display:flex;align-items:center;gap:14px;height:34px;font-size:9.5px;line-height:1.3;color:var(--ink)}
  .topic-icon{width:24px;height:24px;flex:none}
</style>
</head>
<body>
<main class="spread">

  <section class="page page--left">
    <h1 class="page-title">BMCI Project Management Staff</h1>
    <div class="title-rule"></div>
    <p class="intro">Humankind will live together in love, peace, and joy when all people grow to have deeply felt love and regard for all others. This profound change in humankind requires transformed lives, one individual at a time.</p>

    <article class="staff-card" style="left:40px;top:132px">
      <div class="staff-photo photo-portrait-a" role="img" aria-label="Portrait photo of the project director"></div>
      <h3 class="staff-role">Project Director</h3>
      <p class="staff-name">Martin Ellsworth, PhD</p>
      <p class="staff-bio">Dr. Ellsworth is the president of BMCI. His PhD is in supervision and developing educational programs. He is the co-author of Guiding New Mentors and the Workplace Temperament Survey.</p>
    </article>

    <article class="staff-card" style="left:205px;top:160px">
      <div class="staff-photo photo-portrait-b" role="img" aria-label="Portrait photo of the finance lead"></div>
      <h3 class="staff-role">Finance</h3>
      <p class="staff-name">Diane Kessler</p>
      <p class="staff-bio">Diane Kessler was employed for 21 years in public finance, where she received several service honors and was recognized for her outstanding audit and budget work.</p>
    </article>

    <article class="staff-card" style="left:370px;top:188px">
      <div class="staff-photo photo-portrait-c" role="img" aria-label="Portrait photo of the administration lead"></div>
      <h3 class="staff-role">Administration</h3>
      <p class="staff-name">Helen Marsh</p>
      <p class="staff-bio">Helen Marsh has been CEO of a regional medical center, vice president of operations and human resources for a regional production and manufacturing company.</p>
    </article>

    <article class="staff-card" style="left:40px;top:392px">
      <div class="staff-photo photo-portrait-d" role="img" aria-label="Portrait photo of the media lead"></div>
      <h3 class="staff-role">Media</h3>
      <p class="staff-name">Rachel Dunmore</p>
      <p class="staff-bio">Rachel Dunmore is the founder and producer of Open Horizons Radio. She is the author of a memoir that encourages readers to ease the fear of death, move through grief and make the most of their lives every day.</p>
    </article>

    <article class="staff-card" style="left:205px;top:420px">
      <div class="staff-photo photo-portrait-e" role="img" aria-label="Portrait photo of the education lead"></div>
      <h3 class="staff-role">Education</h3>
      <p class="staff-name">Evan Holt</p>
      <p class="staff-bio">Evan is a history, civics, and language arts elementary school teacher. He is a graduate of Midland State University with a BA in English, language arts and teacher education.</p>
    </article>

    <article class="staff-card" style="left:370px;top:448px">
      <div class="staff-photo photo-books" role="img" aria-label="Photo of published book covers"></div>
      <h3 class="staff-role">Publications</h3>
      <p class="staff-name">Northfield Press</p>
      <p class="staff-bio">Northfield Press is a wholly owned publisher that specializes in publishing books by emerging authors in personal growth studies, research and education.</p>
    </article>

    <p class="url">www.brightmeadowcivic.org</p>
    <svg class="wedge" width="340" height="16" viewBox="0 0 340 16"><polygon points="0,0 340,0 340,16 6,5" fill="var(--navy)"/></svg>
  </section>

  <section class="page page--right">
    <div class="hero-photo" role="img" aria-label="Photo of hands typing on a laptop beside a newspaper, notebook and coffee cup"></div>
    <div class="hero-banner"><span>Teaching People to Have</span><strong>AFTERLIFE CONNECTIONS</strong></div>

    <p class="program-text">Martin Ellsworth, president of BMCI, has developed an online training program that enables anyone to connect with loved ones living on the next plane of life. It uses a form of self-relaxation to bring the experiencer into a state in which the connections may occur. It then teaches the experiencer how to allow free, open, unfiltered messages to come through from the loved one. The experiencers fill out journals after each stage that are submitted to BMCI. Martin reads each journal and coaches experiencers to help them learn how to have an afterlife connection by allowing free unfoldment.</p>
    <p class="program-link">The procedure is free on the Internet at this link:</p>
    <p class="program-sub">Quiet Bridge Sessions</p>

    <ul class="topic-list topic-list--a">
      <li><svg class="topic-icon" viewBox="0 0 24 24"><rect x="4" y="4" width="16" height="16" transform="rotate(-12 12 12)" fill="none" stroke="var(--navy)" stroke-width="1.5"/><path d="M8 12l3 3 5-6" fill="none" stroke="var(--navy)" stroke-width="1.8"/></svg>Successes and Validations</li>
      <li><svg class="topic-icon" viewBox="0 0 24 24"><rect x="4" y="4" width="16" height="16" transform="rotate(-12 12 12)" fill="none" stroke="var(--navy)" stroke-width="1.5"/><circle cx="12" cy="10" r="2.5" fill="var(--navy)"/><path d="M7.5 17c1-3 8-3 9 0z" fill="var(--navy)"/></svg>Example Account by an Experiencer</li>
      <li><svg class="topic-icon" viewBox="0 0 24 24"><rect x="4" y="4" width="16" height="16" transform="rotate(-12 12 12)" fill="none" stroke="var(--navy)" stroke-width="1.5"/><path d="M8 15l4-5 4 5M12 10v7" fill="none" stroke="var(--navy)" stroke-width="1.8"/></svg>Future Advancements with Funding</li>
      <li><svg class="topic-icon" viewBox="0 0 24 24"><rect x="4" y="4" width="16" height="16" transform="rotate(-12 12 12)" fill="none" stroke="var(--navy)" stroke-width="1.5"/><text x="12" y="16" text-anchor="middle" font-family="Montserrat, sans-serif" font-weight="700" font-size="10" fill="var(--navy)">$</text></svg>Costs</li>
    </ul>

    <ul class="topic-list topic-list--b">
      <li><svg class="topic-icon" viewBox="0 0 24 24"><rect x="4" y="4" width="16" height="16" transform="rotate(-12 12 12)" fill="none" stroke="var(--navy)" stroke-width="1.5"/><path d="M9 8h6M9 11h6M9 14h4" stroke="var(--navy)" stroke-width="1.5"/></svg>Details about Quiet Bridge Sessions</li>
      <li><svg class="topic-icon" viewBox="0 0 24 24"><rect x="4" y="4" width="16" height="16" transform="rotate(-12 12 12)" fill="none" stroke="var(--navy)" stroke-width="1.5"/><path d="M9 16v-3M12 16v-6M15 16v-4" stroke="var(--navy)" stroke-width="2"/></svg>Project Results</li>
      <li><svg class="topic-icon" viewBox="0 0 24 24"><rect x="4" y="4" width="16" height="16" transform="rotate(-12 12 12)" fill="none" stroke="var(--navy)" stroke-width="1.5"/><circle cx="12" cy="12" r="4.5" fill="none" stroke="var(--navy)" stroke-width="1.5"/><path d="M12 9.5V12h2" fill="none" stroke="var(--navy)" stroke-width="1.5"/></svg>Timeline</li>
    </ul>

    <svg class="wedge" width="360" height="16" viewBox="0 0 360 16"><polygon points="0,0 360,0 354,5 0,16" fill="var(--navy)"/></svg>
    <p class="url">www.brightmeadowcivic.org</p>
  </section>

</main>
</body>
</html>
```